BOLD & MINIMALIST DESIGN NEEDED

We want a very bold but minimalistic business card design that is impactful and utilizes both sides of the business card. Our current logo is included for your use.

We want bold fonts and good use of negative space. We don't want the logo to overpower the design.

Target Market(s)

Professionals who are building new commercial buildings.

Industry/Entity Type

Construction

Contact Information for Business Card

Name, Title, email, office phone, cell phone, website

Font styles to use
Serif
Sans Serif

Requirements
Must have
• Bold design!

```html
<!DOCTYPE html>
<html lang="en">
<head>
<meta charset="utf-8">
<title>Summitline Business Card</title>
<link rel="stylesheet" href="https://fonts.googleapis.com/css2?family=Roboto:wght@400;700;900&display=swap">
<style>
  :root {
    --backdrop: #e2e2e2;
    --card: #303030;
    --ink-light: #ffffff;
    --accent: #7dc42a;
    --shadow: rgba(0, 0, 0, 0.35);
  }
  html, body {
    margin: 0;
    padding: 0;
    width: 1200px;
    height: 1200px;
    overflow: hidden;
    background: var(--backdrop);
    font-family: "Roboto", Arial, sans-serif;
  }
  .canvas {
    position: relative;
    width: 1200px;
    height: 1200px;
  }
  .card {
    position: absolute;
    left: 255px;
    width: 690px;
    height: 394px;
    background: var(--card);
    box-shadow: 0 14px 24px var(--shadow);
  }
  .card--front { top: 160px; }
  .card--back  { top: 652px; }

  .brand-name {
    margin: 0;
    color: var(--ink-light);
    font-weight: 900;
    letter-spacing: 1px;
    line-height: 1;
  }
  .card--front .brand-name {
    position: absolute;
    left: 46px;
    top: 62px;
    font-size: 42px;
  }
  .brand-square {
    position: absolute;
    background: var(--accent);
  }
  .card--front .brand-square {
    left: 430px;
    top: 170px;
    width: 80px;
    height: 80px;
  }

  .person {
    position: absolute;
    left: 46px;
    top: 182px;
  }
  .person-name {
    margin: 0;
    color: var(--accent);
    font-weight: 700;
    font-size: 28px;
    letter-spacing: 0.5px;
    line-height: 1;
  }
  .person-title {
    margin: 8px 0 0;
    color: var(--ink-light);
    font-size: 16px;
  }

  .contact-list {
    position: absolute;
    left: 46px;
    top: 268px;
    margin: 0;
    padding: 0;
    list-style: none;
  }
  .contact-item {
    display: flex;
    align-items: center;
    height: 20.5px;
    color: var(--ink-light);
    font-size: 17px;
  }
  .contact-icon {
    width: 14px;
    height: 14px;
    margin-right: 14px;
    fill: var(--accent);
  }

  .back-brand {
    position: absolute;
    inset: 0;
    display: flex;
    flex-direction: column;
    align-items: center;
    justify-content: center;
    gap: 28px;
  }
  .card--back .brand-square {
    position: static;
    width: 90px;
    height: 90px;
  }
  .card--back .brand-name {
    font-size: 58px;
  }
</style>
</head>
<body>
<main class="canvas">

  <section class="card card--front" aria-label="Card front">
    <h1 class="brand-name">SUMMITLINE</h1>

    <div class="person">
      <p class="person-name">DANIEL REYES</p>
      <p class="person-title">President</p>
    </div>

    <ul class="contact-list">
      <li class="contact-item">
        <svg class="contact-icon" viewBox="0 0 16 16" aria-hidden="true"><path d="M3.6 1l2.6 3-1.5 1.8c.9 2 2.5 3.6 4.5 4.5L11 8.8l3 2.6-1.5 3C6.5 14.5 1.5 9.5 1.6 3.5z"/></svg>
        555-214-7730
      </li>
      <li class="contact-item">
        <svg class="contact-icon" viewBox="0 0 16 16" aria-hidden="true"><path d="M4 0h8a1 1 0 0 1 1 1v14a1 1 0 0 1-1 1H4a1 1 0 0 1-1-1V1a1 1 0 0 1 1-1zm1 2v10h6V2zm3 11a1 1 0 1 0 0 2 1 1 0 0 0 0-2z"/></svg>
        555-309-4418
      </li>
      <li class="contact-item">
        <svg class="contact-icon" viewBox="0 0 16 16" aria-hidden="true"><path d="M0 3h16v10H0zm1.5 1.3v.4L8 9l6.5-4.3v-.4zM1.5 6.4v5.1h13V6.4L8 10.7z"/></svg>
        info@summitline.com
      </li>
      <li class="contact-item">
        <svg class="contact-icon" viewBox="0 0 16 16" aria-hidden="true"><path d="M8 0a8 8 0 1 0 0 16A8 8 0 0 0 8 0zm-1 2.2c-.6 1-1.8 1.3-2.2 2.3-.3.9.8 1.4 1.6 1.5 1 .2 1.3 1.1.9 2-.4.8-1.5 1-1.4 2 .1.9.9 1.6.7 2.6A6 6 0 0 1 7 2.2zm3 .2a6 6 0 0 1 3.8 7c-.6-.4-1.4-.3-1.9.2-.6.6-1.5.3-1.6-.5-.1-.9.8-1.6.6-2.5-.2-.8-1.3-.7-1.6-1.5-.3-.9.4-1.8.7-2.7z"/></svg>
        www.summitline.com
      </li>
    </ul>

    <span class="brand-square" aria-hidden="true"></span>
  </section>

  <section class="card card--back" aria-label="Card back">
    <div class="back-brand">
      <span class="brand-square" aria-hidden="true"></span>
      <h2 class="brand-name">SUMMITLINE</h2>
    </div>
  </section>

</main>
</body>
</html>
```